Small corporate website template design

I need a couple templates designed for a small corporate website. The corporate site reflects the existence of the parent company which will own various brands/services that have their own websites, so it will mainly be used to present who we are, what we do, what is happening (news/events), how to contact us, link off to our other brand/service sites, as well as post information for public relations, investors, and job opportunities.

The company name is Brelvanto LLC (www.brelvanto-example.com), and the name is representative of stratified layers of interconnected digital services. The corporate site is not expected to generate a bunch of fanfare - that honor will be reserved for the externally linked brand/service sites.

The provided logo may be manipulated in color, size, shape, positioning, etc. to get it to fit with the design, but should be integrated in some way.

What we are looking for is a home page layout as well as a template for an inner page whereby the navigation/logo, etc may be diminished to some extent for the inner pages. We are also interested in reusable elements such as dividers, content containers, etc. in order to represent the types of information described above that we would like to present as described above.

We are particularly interested in consistency of design elements, conservative use of color (including consideration of accessibility concerns), judicious use of whitespace in favor of simplified messaging, and something lending itself well to internationalization/translation.

Target Market(s)

Small business owners, entrepreneurs (B2B)

Number of Pages Required

2 page

Font styles to use
Sans Serif

Requirements
Must have
• See the attached PDF with the logo concept, color swatches, and comparative sites.

```html
<!DOCTYPE html>
<html lang="en">
<head>
<meta charset="utf-8">
<title>Brelvanto LLC</title>
<link rel="stylesheet" href="https://fonts.googleapis.com/css2?family=Signika:wght@400;600&family=Arimo:wght@400;700&display=swap">
<style>
  :root {
    --navy: #0b3166;
    --navy-deep: #082a58;
    --sky: #4d80c2;
    --ink: #3e3e3e;
    --muted: #7a7a7a;
    --line: #c9c9c9;
    --white: #ffffff;
    --photo-a: #8a8178;
    --photo-b: #5d5a58;
  }
  * { box-sizing: border-box; margin: 0; padding: 0; }
  html, body { width: 1200px; height: 3774px; overflow: hidden; }
  body { position: relative; background: var(--white); font-family: "Arimo", Arial, sans-serif; color: var(--ink); }
  .abs { position: absolute; }
  .heading { font-family: "Signika", "Arimo", sans-serif; font-weight: 400; }
  .photo { background: linear-gradient(135deg, var(--photo-a), var(--photo-b)); }
  .btn { display: flex; align-items: center; justify-content: center; background: var(--navy); color: var(--white); font-size: 19px; text-transform: uppercase; }

  /* header */
  .topbar { left: 0; top: 35px; width: 1200px; height: 55px; background: var(--navy); }
  .brand { left: 30px; top: 12px; width: 150px; height: 96px; background: var(--white); display: flex; align-items: center; justify-content: center; text-align: center; color: var(--navy); font-weight: 700; font-size: 22px; line-height: 1.15; }
  .nav { left: 0; top: 35px; width: 900px; height: 55px; }
  .nav a { position: absolute; top: 0; height: 55px; line-height: 55px; color: var(--white); text-decoration: none; font-size: 16px; white-space: nowrap; }
  .quote-btn { left: 938px; top: 38px; width: 136px; height: 50px; background: var(--white); color: var(--navy); font-size: 19px; display: flex; align-items: center; justify-content: center; }
  .search { left: 1094px; top: 44px; }

  /* hero */
  .hero { left: 0; top: 120px; width: 1200px; height: 640px; }
  .hero-shade { left: 0; top: 120px; width: 1200px; height: 640px; background: rgba(30,30,40,.35); }
  .hero-title { left: 0; width: 1200px; top: 340px; text-align: center; color: var(--white); font-size: 54px; }
  .hero-btn { left: 526px; top: 444px; width: 148px; height: 48px; font-size: 18px; }
  .hero-cut { left: 0; top: 640px; }
  .down-dot { left: 578px; top: 724px; }

  /* welcome */
  .welcome-small { left: 80px; top: 822px; font-size: 40px; color: var(--sky); }
  .welcome-big { left: 80px; top: 868px; font-size: 46px; color: var(--navy); }
  .welcome-copy { left: 80px; top: 952px; width: 540px; font-size: 15px; line-height: 26px; color: #555; }
  .welcome-btn { left: 78px; top: 1108px; width: 146px; height: 52px; }
  .welcome-frame { left: 696px; top: 830px; width: 426px; height: 330px; background: var(--navy); }
  .welcome-photo { left: 716px; top: 850px; width: 406px; height: 310px; }

  /* services */
  .band { left: 0; }
  .band-title { left: 0; width: 1200px; text-align: center; color: var(--white); font-size: 42px; }
  .service { width: 300px; text-align: center; color: var(--white); }
  .service svg { display: block; margin: 0 auto 20px; }
  .service h3 { font-size: 17px; font-weight: 400; margin-bottom: 12px; }
  .service p { font-size: 15px; line-height: 27px; }
  .service a { display: inline-block; margin-top: 6px; color: var(--white); font-size: 15px; text-decoration: underline; }

  /* news */
  .news-title { left: 0; width: 1200px; top: 1768px; text-align: center; font-size: 42px; color: var(--navy); }
  .news-intro { left: 284px; top: 1846px; width: 634px; text-align: center; font-size: 15px; line-height: 28px; color: #555; }
  .card { top: 1925px; width: 322px; height: 435px; background: var(--white); box-shadow: 0 4px 14px rgba(0,0,0,.16); }
  .card .photo { width: 100%; height: 309px; }
  .card h3 { padding: 22px 14px 0; font-size: 17px; line-height: 30px; color: var(--navy); font-weight: 400; }
  .card .meta { position: absolute; left: 14px; right: 14px; bottom: 12px; display: flex; justify-content: space-between; font-size: 14px; color: var(--muted); }
  .card .meta span { display: flex; align-items: center; gap: 8px; }

  /* testimonial */
  .quote-box { left: 236px; top: 2561px; width: 728px; height: 144px; border: 1.5px solid #c9d5e6; }
  .quote-text { left: 318px; top: 2572px; width: 564px; text-align: center; color: var(--white); font-size: 15px; line-height: 30px; }
  .quote-mark { color: var(--white); font-family: "Signika", serif; font-size: 120px; line-height: 1; font-weight: 600; }
  .avatar { border: 3px solid var(--white); }
  .client-name { left: 0; width: 1200px; top: 2860px; text-align: center; color: var(--white); font-size: 15px; font-weight: 700; }
  .pager { width: 30px; height: 30px; background: var(--white); display: flex; align-items: center; justify-content: center; }

  /* contact */
  .contact-title { left: 80px; top: 3012px; font-size: 44px; color: var(--navy); }
  .field { border: 1px solid var(--line); font-size: 15px; color: #666; padding: 16px 12px; }
  .submit { left: 78px; top: 3323px; width: 654px; height: 53px; }
  .info { left: 800px; font-size: 15px; line-height: 27px; color: #555; display: flex; gap: 22px; }
  .info svg { flex: none; margin-top: 6px; }

  /* footer */
  .footer { left: 0; top: 3439px; width: 1200px; height: 335px; background: var(--navy-deep); }
  .footer-brand { left: 0; width: 1200px; top: 3505px; text-align: center; color: var(--white); font-weight: 700; font-size: 30px; }
  .footer-nav { left: 0; width: 1200px; top: 3598px; display: flex; justify-content: center; gap: 24px; color: var(--white); font-size: 15px; }
  .social { left: 524px; top: 3650px; display: flex; gap: 14px; }
  .social span { width: 42px; height: 42px; border: 2px solid var(--white); border-radius: 50%; display: block; }
  .social span:first-child { background: var(--white); }
  .footer-rule { left: 78px; top: 3714px; width: 1044px; height: 1px; background: #5b79a3; }
  .copyright { left: 0; width: 1200px; top: 3733px; text-align: center; color: var(--white); font-size: 14px; }
</style>
</head>
<body>

<header>
  <div class="abs topbar"></div>
  <div class="abs brand">Brelvanto<br>LLC</div>
  <nav class="abs nav">
    <a style="left:194px">Home</a>
    <a style="left:299px">About Us</a>
    <a style="left:430px">Services</a>
    <a style="left:556px">News</a>
    <a style="left:662px">Contact Us</a>
  </nav>
  <div class="abs quote-btn">GET A QUOTE</div>
  <svg class="abs search" width="36" height="36" viewBox="0 0 36 36" aria-label="Search"><circle cx="14" cy="14" r="10" fill="none" stroke="#fff" stroke-width="3.5"/><line x1="21" y1="21" x2="32" y2="32" stroke="#fff" stroke-width="4" stroke-linecap="round"/></svg>
</header>

<section class="hero-section">
  <div class="abs hero photo" role="img" aria-label="Photo of a team working together around a desk with a monitor"></div>
  <div class="abs hero-shade"></div>
  <h1 class="abs hero-title heading">Welcome To Brelvanto LLC</h1>
  <div class="abs btn hero-btn">Contact Us</div>
  <svg class="abs hero-cut" width="1200" height="130" viewBox="0 0 1200 130"><polygon points="0,10 600,90 1200,10 1200,130 0,130" fill="#fff"/></svg>
  <svg class="abs down-dot" width="44" height="44" viewBox="0 0 44 44" aria-label="Scroll down"><circle cx="22" cy="22" r="21" fill="#0b3166"/><path d="M22 12v19M14 23l8 8 8-8" fill="none" stroke="#fff" stroke-width="3"/></svg>
</section>

<section class="welcome">
  <h2 class="abs welcome-small heading">Welcome To</h2>
  <h2 class="abs welcome-big heading">Brelvanto LLC</h2>
  <p class="abs welcome-copy">Lorem Ipsum is simply dummy text of the printing and typesetting industry. Lorem Ipsum has been the industry's standard dummy text ever since the 1500s, when an unknown printer took a galley of type and scrambled it to make a type specimen book. It has survived not only five centuries, but also the leap into electronic typesetting, remaining essentially unchanged.</p>
  <div class="abs btn welcome-btn">Learn More</div>
  <div class="abs welcome-frame"></div>
  <div class="abs welcome-photo photo" role="img" aria-label="Photo of colleagues in a meeting reviewing charts" style="background:linear-gradient(135deg,#c7cbd1,#7f8894)"></div>
</section>

<section class="services">
  <svg class="abs band" style="top:1223px" width="1200" height="488" viewBox="0 0 1200 488"><polygon points="0,0 1200,0 1200,395 600,488 0,395" fill="#0b3166"/></svg>
  <h2 class="abs band-title heading" style="top:1280px">Our Services</h2>

  <div class="abs service" style="left:89px;top:1355px">
    <svg width="82" height="64" viewBox="0 0 82 64" aria-label="Target icon"><circle cx="34" cy="34" r="26" fill="none" stroke="#fff" stroke-width="5"/><circle cx="34" cy="34" r="15" fill="none" stroke="#fff" stroke-width="5"/><circle cx="34" cy="34" r="5" fill="#fff"/><path d="M34 34 70 8" stroke="#fff" stroke-width="4"/><path d="M64 4l10 0-4 10z" fill="#fff"/></svg>
    <h3>Marketing Strategy</h3>
    <p>Lorem Ipsum is simply dummy text of the printing and typesetting industry. Lorem Ipsum has been the industry's</p>
    <a>Read More...</a>
  </div>
  <div class="abs service" style="left:449px;top:1355px">
    <svg width="82" height="64" viewBox="0 0 82 64" aria-label="Analytics screen icon"><rect x="6" y="4" width="70" height="46" rx="3" fill="none" stroke="#fff" stroke-width="4"/><path d="M14 40l12-14 10 8 12-18 10 12 10-8" fill="none" stroke="#fff" stroke-width="3"/><rect x="30" y="52" width="22" height="6" fill="#fff"/></svg>
    <h3>Digital Analytics</h3>
    <p>Lorem Ipsum is simply dummy text of the printing and typesetting industry. Lorem Ipsum has been the industry's</p>
    <a>Read More...</a>
  </div>
  <div class="abs service" style="left:814px;top:1355px">
    <svg width="82" height="64" viewBox="0 0 82 64" aria-label="Gears icon"><circle cx="28" cy="22" r="12" fill="none" stroke="#fff" stroke-width="8" stroke-dasharray="6 4"/><circle cx="28" cy="22" r="7" fill="none" stroke="#fff" stroke-width="3"/><circle cx="54" cy="42" r="14" fill="none" stroke="#fff" stroke-width="8" stroke-dasharray="6 4"/><text x="54" y="48" fill="#fff" font-size="16" font-family="Arimo,sans-serif" text-anchor="middle" font-weight="700">$</text></svg>
    <h3>Management and Optimization</h3>
    <p>Lorem Ipsum is simply dummy text of the printing and typesetting industry. Lorem Ipsum has been the industry's</p>
    <a>Read More...</a>
  </div>
</section>

<section class="news">
  <h2 class="abs news-title heading">Latest News</h2>
  <p class="abs news-intro">Lorem Ipsum is simply dummy text of the printing and typesetting industry. Lorem Ipsum has been the industry's standard dummy text ever since the 1500s,</p>

  <article class="abs card" style="left:78px">
    <div class="photo" role="img" aria-label="Photo of a team gathered around a laptop" style="background:linear-gradient(135deg,#d9d6d2,#6b5c55)"></div>
    <h3>Lorem Ipsum is simply dummy text of the printing and typesetting.</h3>
    <div class="meta"><span><svg width="20" height="16" viewBox="0 0 20 16"><path d="M2 2h16v9H8l-4 4v-4H2z" fill="none" stroke="#888" stroke-width="1.6"/></svg>7 Comments</span><span><svg width="18" height="16" viewBox="0 0 18 16"><path d="M9 15S1 10 1 5a4 4 0 0 1 8-1 4 4 0 0 1 8 1c0 5-8 10-8 10z" fill="none" stroke="#888" stroke-width="1.6"/></svg>32 Likes</span></div>
  </article>
  <article class="abs card" style="left:440px">
    <div class="photo" role="img" aria-label="Photo of hands typing on a laptop" style="background:linear-gradient(135deg,#e4e4e4,#4d4f52)"></div>
    <h3>Lorem Ipsum is simply dummy text of the printing and typesetting.</h3>
    <div class="meta"><span><svg width="20" height="16" viewBox="0 0 20 16"><path d="M2 2h16v9H8l-4 4v-4H2z" fill="none" stroke="#888" stroke-width="1.6"/></svg>7 Comments</span><span><svg width="18" height="16" viewBox="0 0 18 16"><path d="M9 15S1 10 1 5a4 4 0 0 1 8-1 4 4 0 0 1 8 1c0 5-8 10-8 10z" fill="none" stroke="#888" stroke-width="1.6"/></svg>32 Likes</span></div>
  </article>
  <article class="abs card" style="left:800px">
    <div class="photo" role="img" aria-label="Photo of colleagues looking at a tablet" style="background:linear-gradient(135deg,#3a4a63,#8c7a6b)"></div>
    <h3>Lorem Ipsum is simply dummy text of the printing and typesetting.</h3>
    <div class="meta"><span><svg width="20" height="16" viewBox="0 0 20 16"><path d="M2 2h16v9H8l-4 4v-4H2z" fill="none" stroke="#888" stroke-width="1.6"/></svg>7 Comments</span><span><svg width="18" height="16" viewBox="0 0 18 16"><path d="M9 15S1 10 1 5a4 4 0 0 1 8-1 4 4 0 0 1 8 1c0 5-8 10-8 10z" fill="none" stroke="#888" stroke-width="1.6"/></svg>32 Likes</span></div>
  </article>
</section>

<section class="testimonial">
  <svg class="abs band" style="top:2423px" width="1200" height="533" viewBox="0 0 1200 533"><polygon points="0,0 1200,0 1200,440 600,533 0,440" fill="#0b3166"/></svg>
  <h2 class="abs band-title heading" style="top:2478px">Client Testimonial</h2>
  <div class="abs quote-box"></div>
  <div class="abs quote-mark" style="left:212px;top:2532px;background:#0b3166;padding:0 6px;height:62px;overflow:hidden">&ldquo;</div>
  <div class="abs quote-mark" style="left:922px;top:2660px;background:#0b3166;padding:0 6px;height:62px;overflow:hidden">&rdquo;</div>
  <p class="abs quote-text">Lorem Ipsum is simply dummy text of the printing and typesetting industry. Lorem Ipsum has been the industry's standard dummy text ever since the 1500s, when an unknown printer took a galley of type and scrambled it to make a type specimen book.</p>
  <svg class="abs" style="left:587px;top:2713px" width="26" height="26" viewBox="0 0 26 26"><path d="M5 4l8 8 8-8M5 13l8 8 8-8" fill="none" stroke="#fff" stroke-width="2.5"/></svg>

  <div class="abs pager" style="left:413px;top:2778px"><svg width="16" height="14" viewBox="0 0 16 14"><path d="M8 1 2 7l6 6M14 1 8 7l6 6" fill="none" stroke="#0b3166" stroke-width="2.2"/></svg></div>
  <div class="abs avatar photo" role="img" aria-label="Client portrait" style="left:473px;top:2766px;width:64px;height:64px;background:linear-gradient(135deg,#d8c9bd,#8f7466)"></div>
  <div class="abs avatar photo" role="img" aria-label="Client portrait, selected" style="left:560px;top:2758px;width:80px;height:80px;background:linear-gradient(135deg,#bfc6cf,#3b4352)"></div>
  <div class="abs avatar photo" role="img" aria-label="Client portrait" style="left:663px;top:2766px;width:64px;height:64px;background:linear-gradient(135deg,#c9c4bf,#5b5550)"></div>
  <div class="abs pager" style="left:757px;top:2778px"><svg width="16" height="14" viewBox="0 0 16 14"><path d="M2 1l6 6-6 6M8 1l6 6-6 6" fill="none" stroke="#0b3166" stroke-width="2.2"/></svg></div>
  <p class="abs client-name">- CLIENT NAME</p>
</section>

<section class="contact">
  <h2 class="abs contact-title heading">Contact Us</h2>
  <div class="abs field" style="left:78px;top:3087px;width:320px;height:50px">Name*</div>
  <div class="abs field" style="left:410px;top:3087px;width:322px;height:50px">E-mail*</div>
  <div class="abs field" style="left:78px;top:3150px;width:320px;height:50px">Phone*</div>
  <div class="abs field" style="left:410px;top:3150px;width:322px;height:50px">Subject</div>
  <div class="abs field" style="left:78px;top:3213px;width:654px;height:102px">Message</div>
  <div class="abs btn submit">Submit</div>

  <div class="abs info" style="top:3158px"><svg width="14" height="18" viewBox="0 0 14 18"><path d="M7 17S1 10 1 6.5a6 6 0 0 1 12 0C13 10 7 17 7 17z" fill="#0b3166"/><circle cx="7" cy="6.5" r="2.2" fill="#fff"/></svg><span>123.Lorem Ipsum is simply<br>dummy text of the printing</span></div>
  <div class="abs info" style="top:3236px"><svg width="16" height="16" viewBox="0 0 16 16"><path d="M3 1l3 3-2 2c1 2 4 5 6 6l2-2 3 3-2 2C7 15 1 9 1 3z" fill="#0b3166"/></svg><span>123 456 7890</span></div>
  <div class="abs info" style="top:3285px"><svg width="16" height="12" viewBox="0 0 16 12"><rect x="0" y="0" width="16" height="12" fill="#0b3166"/><path d="M1 1l7 6 7-6" fill="none" stroke="#fff" stroke-width="1.4"/></svg><span>info@brelvanto-example.com</span></div>
</section>

<footer>
  <div class="abs footer"></div>
  <div class="abs footer-brand">Brelvanto LLC</div>
  <div class="abs footer-nav"><span>Home</span><span>|</span><span>About Us</span><span>|</span><span>Services</span><span>|</span><span>News</span><span>|</span><span>Contact us</span></div>
  <div class="abs social" role="img" aria-label="Social media links"><span></span><span></span><span></span></div>
  <div class="abs footer-rule"></div>
  <p class="abs copyright">&copy;BRELVANTO LLC - 2018. All Rights Reserved.</p>
</footer>

</body>
</html>
```